Emerging automotive detailing business

I am starting a small automotive detailing business in hopes of becoming a well-known detailer to work on high end cars. I would like a card to reflect the high quality and time I put into my work. The name of the company is Bright Crest Detailing. I feel like it represents racecars getting off the line at the drag strip as well as an innuendo of "Up the Ladder". I do minor paint correction such as clay barring, multi-step buffing and polishing, waxing, hand washes, etc. I am always striving to learn more and improve my work. My goal is to have total customer satisfaction. This is a female run business but I do not want it to be very girly. Elegant is okay! I have pictures of my personal wrenfield attached, they do not need to be incorporated but if you can think of a cool way to use 1 or all of them, go for it!

Target Market(s)

Anyone that owns a vehicle. Preferably high end vehicles such as Valtori, Castellverde and Morvani but I will also happily work on any car, truck or suv no matter what brand.

Industry/Entity Type

Automotive

Contact Information for Business Card

Bright Crest Detailing
Mira Tolland
4175 Quenhollow Rd
Ashmere PA 17492
Cell phone- call/text- 717-555-0148
email- brightcrestdetails@maildrop-example.com
Instagram: @brightcrestdetailing
Facebook: facebook.com/brightcrestdetailing

Requirements
Must have
• Business name, my name, address, phone number. Listing that I do minor paint correction such as clay barring, multi-step buffing and polishing, waxing, hand washes, interior cleaning, and more. (This last part was in nice to haves but I have realized that I do really want it, so I moved it to must haves.) I want something that is different and eye-catching to my customers. Some people have done this very well with cards already submitted to me, but a lot have not. I didn't mess with the "look and feel bars" much because because I am pretty open to the overall design as long as it is not your basic run of the mill design.
Nice to have
• Something car related. Maybe an appointment time/date line. I do not have a logo, but if you would like to design one and incorporate it, that would be amazing!
Should not have
• Purple and Pink colors. Boring, basic, normal card.

```html
<!DOCTYPE html>
<html lang="en">
<head>
<meta charset="utf-8">
<title>Bright Crest Detailing – Business Card</title>
<link rel="stylesheet" href="https://fonts.googleapis.com/css2?family=Open+Sans:wght@400;600;700&display=swap">
<style>
  :root {
    --backdrop: #2c2e33;
    --card-white: #ffffff;
    --brand-red: #e01b24;
    --ink: #111111;
    --band-black: #0c0c0c;
    --faint-grey: #e3e3e5;
    --faint-ring: #f1f1f2;
    --dot-line: #333333;
    --muted: #555555;
  }
  * { box-sizing: border-box; margin: 0; padding: 0; }
  html, body {
    width: 1200px; height: 864px; overflow: hidden;
    background: var(--backdrop);
    font-family: "Open Sans", Arial, sans-serif;
    color: var(--ink);
  }
  .card-set {
    position: absolute; inset: 0;
    display: flex; flex-direction: column; align-items: center; justify-content: center;
    gap: 44px;
  }
  .card {
    position: relative; width: 640px; height: 366px;
    background: var(--card-white); overflow: hidden;
    border-top: 14px solid var(--brand-red);
    border-bottom: 16px solid var(--band-black);
  }
  .brand {
    position: absolute; display: flex; align-items: flex-start; gap: 10px;
    color: var(--ink); font-weight: 400;
  }
  .brand-mark {
    width: 38px; height: 38px; border-radius: 50%;
    background: var(--brand-red); flex: none; margin-top: 4px;
  }
  .brand-name { line-height: 1; }
  .brand-name .primary { display: block; font-size: 40px; letter-spacing: 3px; }
  .brand-name .secondary { display: block; font-size: 24px; letter-spacing: 2px; text-align: right; margin-top: 6px; }

  /* Appointment face */
  .card--appointment .brand { top: 30px; left: 150px; }
  .appointment-heading {
    position: absolute; top: 142px; left: 0; right: 0; text-align: center;
    font-size: 19px; font-weight: 600;
  }
  .appointment-field {
    position: absolute; left: 104px; right: 110px;
    display: flex; align-items: flex-end; gap: 12px;
    color: var(--brand-red); font-size: 14px; font-weight: 600;
  }
  .appointment-field .label { width: 50px; }
  .appointment-field .fill {
    flex: 1; border-bottom: 2px dotted var(--dot-line); height: 14px;
  }
  .field-date { top: 196px; }
  .field-time { top: 232px; }
  .service-list {
    position: absolute; left: 40px; right: 40px; bottom: 22px;
    text-align: center; font-size: 12px; line-height: 1.5; color: var(--muted);
  }
  .service-list .lead { color: var(--brand-red); font-weight: 600; }

  /* Contact face */
  .card--contact .brand { top: 22px; left: 22px; }
  .card--contact .brand-name .primary { font-size: 42px; }
  .faint-circle {
    position: absolute; right: -70px; top: 54px;
    width: 330px; height: 330px; border-radius: 50%;
    background: var(--faint-grey);
    border: 12px solid var(--faint-ring);
  }
  .owner-name {
    position: absolute; top: 108px; left: 70px;
    color: var(--brand-red); font-size: 19px; font-weight: 700;
  }
  .address {
    position: absolute; top: 150px; left: 60px;
    font-size: 15px; line-height: 1.4;
  }
  .contact-list {
    position: absolute; top: 226px; left: 44px; list-style: none;
    font-size: 15px; line-height: 1.45;
  }
  .contact-list li { display: flex; align-items: center; gap: 12px; }
  .contact-list svg, .contact-list .icon-box { width: 13px; height: 13px; flex: none; }
  .icon-box { background: var(--brand-red); border-radius: 3px; }
</style>
</head>
<body>
<main class="card-set">
  <section class="card card--appointment" aria-label="Appointment card">
    <div class="brand">
      <span class="brand-mark"></span>
      <span class="brand-name"><span class="primary">BRIGHT CREST</span><span class="secondary">Detailing</span></span>
    </div>
    <h2 class="appointment-heading">Your Next Appointment is</h2>
    <div class="appointment-field field-date"><span class="label">Date :</span><span class="fill"></span></div>
    <div class="appointment-field field-time">
      <span class="label">Time:</span><span class="fill"></span><span>AM</span><span class="fill"></span><span>PM</span>
    </div>
    <p class="service-list">
      <span class="lead">Minor paint correction</span> · Clay barring · Multi-step buffing &amp; polishing<br>
      Waxing · Hand washes · Interior cleaning · and more
    </p>
  </section>

  <section class="card card--contact" aria-label="Contact card">
    <div class="faint-circle" role="img" aria-label="Faint car silhouette decoration inside a grey circle"></div>
    <div class="brand">
      <span class="brand-mark"></span>
      <span class="brand-name"><span class="primary">BRIGHT CREST</span><span class="secondary">Detailing</span></span>
    </div>
    <p class="owner-name">Mira Tolland</p>
    <p class="address">4175 Quenhollow Rd<br>Ashmere PA 17492</p>
    <ul class="contact-list">
      <li>
        <svg viewBox="0 0 24 24" aria-hidden="true"><path fill="#e01b24" d="M6.6 10.8a15.1 15.1 0 0 0 6.6 6.6l2.2-2.2c.3-.3.7-.4 1-.2 1.1.4 2.3.6 3.6.6.6 0 1 .4 1 1V20c0 .6-.4 1-1 1C10.6 21 3 13.4 3 4c0-.6.4-1 1-1h3.5c.6 0 1 .4 1 1 0 1.3.2 2.5.6 3.6.1.3 0 .7-.2 1z"/></svg>
        <span>call/text- 717-555-0148</span>
      </li>
      <li>
        <svg viewBox="0 0 24 24" aria-hidden="true"><rect x="2" y="5" width="20" height="14" rx="1" fill="#e01b24"/><path d="M2 6l10 7 10-7" fill="none" stroke="#fff" stroke-width="2"/></svg>
        <span>brightcrestdetails@maildrop-example.com</span>
      </li>
      <li>
        <span class="icon-box"></span>
        <span>@brightcrestdetailing</span>
      </li>
    </ul>
  </section>
</main>
</body>
</html>
```